new letterhead for my brokergae company KeelBright, Complete Marine Brokering

We need a new letterhead for our brokerage company called KeelBright. We are specialised in selling pleasure crafts (sailing and motoryachts). More info can be found at https://keelbright-example.com/en

I use this document for a quotation, a letter, sales agreement, selling instructions. I am looking for a cover page + a content page.

Th efollowing information needs to be in the header / footer; email, website, VAT number, Bank Account number, number chamber of ccomerce, registry number olpa, General terms and conditions TQRV apply.

```html
<!DOCTYPE html>
<html lang="en">
<head>
<meta charset="utf-8">
<title>KeelBright Letterhead</title>
<link rel="stylesheet" href="https://fonts.googleapis.com/css2?family=Open+Sans:wght@400;600;700&display=swap">
<style>
  :root {
    --backdrop: #6fa6de;
    --paper: #ffffff;
    --mist: #e9eef6;
    --navy: #2a4f9e;
    --brand: #1f5aa8;
    --orange: #ec5a2c;
    --peach: #f8dccd;
    --steel: #9c9fa4;
    --ink: #3a3d44;
    --label-bg: #e3e5e8;
  }
  * { margin: 0; padding: 0; box-sizing: border-box; }
  html, body { width: 1200px; height: 784px; overflow: hidden; }
  body {
    background: var(--backdrop);
    font-family: "Open Sans", Arial, sans-serif;
    display: flex; align-items: center; justify-content: center;
  }
  .letterhead {
    position: relative;
    width: 524px; height: 742px;
    background: var(--paper);
    box-shadow: 0 6px 18px rgba(20, 50, 100, .28);
    overflow: hidden;
  }
  .letterhead__art { position: absolute; inset: 0; width: 100%; height: 100%; }
  .brand {
    position: absolute; top: 68px; right: 40px;
    text-align: right;
  }
  .brand__name {
    display: flex; align-items: center; gap: 7px; justify-content: flex-end;
    font-size: 28px; font-weight: 700; color: var(--brand); letter-spacing: -.3px;
    line-height: 1;
  }
  .brand__dot { width: 12px; height: 12px; border-radius: 50%; background: var(--brand); }
  .brand__tagline {
    margin-top: 5px;
    font-size: 7.5px; font-weight: 600; letter-spacing: 2px; color: var(--brand);
    text-transform: uppercase;
  }
  .info {
    position: absolute; left: 30px; width: 200px;
    font-size: 7px; color: var(--ink); line-height: 1.75;
  }
  .info--contact { top: 520px; }
  .info--general { top: 590px; left: 96px; }
  .info__label {
    display: inline-block; margin-bottom: 5px;
    padding: 1px 7px; background: var(--label-bg);
    border-left: 2px solid var(--navy); border-right: 2px solid var(--navy);
    font-weight: 700; font-size: 7.5px;
  }
  .info__list { list-style: none; }
  .info__list li { display: flex; align-items: center; gap: 6px; }
  .info__list li::before {
    content: ""; width: 5px; height: 5px; border-radius: 50%;
    background: var(--brand); flex: none;
  }
  .terms { margin-top: 3px; font-style: normal; color: var(--steel); }
</style>
</head>
<body>
  <main class="letterhead">
    <svg class="letterhead__art" viewBox="0 0 524 742" aria-hidden="true">
      <!-- header wash and curves -->
      <path d="M260 0 H524 V160 C470 120 380 60 260 0 Z" fill="var(--mist)"/>
      <path d="M230 8 C330 70 430 110 524 190" fill="none" stroke="var(--mist)" stroke-width="10"/>
      <path d="M250 60 C360 110 440 140 524 200" fill="none" stroke="var(--peach)" stroke-width="3"/>
      <path d="M200 30 C320 95 420 120 524 175" fill="none" stroke="#dfe6f1" stroke-width="2"/>
      <!-- header rule -->
      <line x1="0" y1="8" x2="300" y2="8" stroke="var(--steel)" stroke-width="5"/>
      <rect x="500" y="130" width="8" height="48" fill="var(--navy)"/>
      <!-- footer wash -->
      <path d="M0 742 V560 C60 620 180 690 330 742 Z" fill="#eef3fb"/>
      <!-- info dividers -->
      <line x1="22" y1="508" x2="230" y2="508" stroke="#c9ccd1" stroke-width=".8"/>
      <line x1="88" y1="580" x2="240" y2="660" stroke="#c9ccd1" stroke-width=".8"/>
      <!-- left edge bands -->
      <rect x="0" y="480" width="9" height="262" fill="var(--navy)"/>
      <rect x="9" y="560" width="5" height="60" fill="var(--orange)"/>
      <rect x="9" y="625" width="4" height="117" fill="var(--steel)"/>
    </svg>

    <header class="brand">
      <div class="brand__name"><span class="brand__dot"></span>KeelBright</div>
      <div class="brand__tagline">Complete Marine Brokering</div>
    </header>

    <section class="info info--contact">
      <div class="info__label">Contact Details:</div>
      <ul class="info__list">
        <li>Havenkade 12, 4811 AB Zeewolde</li>
        <li>+31 (0)10 555 01 24</li>
        <li>contact@keelbright-example.com</li>
        <li>www.keelbright-example.com</li>
      </ul>
    </section>

    <section class="info info--general">
      <div class="info__label">General Information:</div>
      <ul class="info__list">
        <li>VAT number: 123456789</li>
        <li>Bank Account Number: 123456789</li>
        <li>Number Chamber of commerce: 123456789</li>
        <li>Registry number OLPA: 123456789</li>
      </ul>
      <p class="terms">General terms and conditions TQRV apply.</p>
    </section>
  </main>
</body>
</html>
```